zAvora Corporate Website

zAvora is a well-funded start up developing an Online Marketing Platform for small businesses in Europe.
We are launching in February 2012 with all-in-one online marketing services including professional website, DIY SEO, Dashboard with Reports and Online marketing tools, and Support.
Our internal web designer has come up with a preliminary website design which we wish to continue to improve using new ideas, colours, layout, image, etc.
The brief is very simple - improve the website whether it is look & feel, ease of use, conversion rate - we are looking for overall improvements.
The contest will last 5 days and we will award the winner £300.
If you are the winner , you will also be required to provide designs for 3 more internal pages adhering to the proposed home page design.
Judging criteria : -
Visual Design
Layout must adhere to best practices and wire frame. If you decide to move elements around significantly please provide reason
Functional, informative and drives calls to action
Industry/Entity Type
Marketing
Look and feel
Each slider illustrates characteristics of the customer's brand and the style your logo design should communicate.

```html
<!DOCTYPE html>
<html lang="en">
<head>
<meta charset="utf-8">
<title>zAvora – Online Marketing for Small Business</title>
<link rel="stylesheet" href="https://fonts.googleapis.com/css2?family=Roboto:wght@300;400;500;700&family=Anton&display=swap">
<style>
:root{
  --sky:#bfe4fa;
  --band:#a6d4f1;
  --page:#edf4fa;
  --blue:#2b8ee0;
  --blue-deep:#1262c9;
  --link:#37a4e6;
  --ink:#222;
  --text:#3a3a3a;
  --card-border:#d6e6f2;
  --orange:#ff9a10;
  --footer:#1d1d1d;
  --footer-line:#333;
  --footer-text:#bdbdbd;
  --green:#4fa019;
}
*{margin:0;padding:0;box-sizing:border-box}
html,body{width:818px;height:1200px;overflow:hidden}
body{position:relative;font-family:"Roboto",Arial,sans-serif;color:var(--text);
  background:linear-gradient(var(--sky) 0,var(--sky) 352px,var(--band) 352px,var(--band) 432px,var(--page) 432px)}
.abs{position:absolute}
.top-bar{left:0;top:0;width:818px;height:4px;background:#222}
.top-nav{left:546px;top:0;width:162px;height:22px;background:#222;border-radius:0 0 10px 10px;
  color:#fff;font-size:7px;display:flex;justify-content:center;align-items:center;gap:9px;letter-spacing:.2px}
.top-nav span.sep{color:#888}
.brand{left:108px;top:32px;display:flex;align-items:center;gap:8px}
.brand-dot{width:44px;height:44px;border-radius:50%;background:var(--blue)}
.brand-name{font-size:38px;font-weight:400;color:#111;letter-spacing:-.5px}
.menu{left:544px;top:62px;width:160px;height:26px;border-radius:4px;background:linear-gradient(#f4f4f4,#d9d9d9);
  display:flex;align-items:center;font-size:9px;color:#222;box-shadow:0 1px 2px rgba(0,0,0,.2)}
.menu .home{width:40px;height:26px;background:linear-gradient(#3aa0f0,#1667d0);border-radius:4px 0 0 4px;display:flex;align-items:center;justify-content:center}
.menu span{padding:0 8px;border-right:1px solid #bbb}
.menu span:last-child{border:none}
.hero{left:102px;top:98px;width:612px;height:236px;border:2px solid #fff;border-radius:6px;overflow:hidden;
  background:radial-gradient(circle at 30% 40%,#3d9af2,#1863dc 70%);box-shadow:0 4px 10px rgba(0,0,0,.15)}
.hero h1{position:absolute;left:56px;top:18px;color:#fff;font-size:21px;font-weight:700;line-height:23px;text-shadow:0 1px 2px rgba(0,0,0,.35)}
.hero ul{position:absolute;left:56px;top:80px;list-style:none;color:#fff;font-size:13px;font-weight:500}
.hero li{height:23px;display:flex;align-items:center;gap:12px}
.hero li svg{width:16px;height:12px}
.cta{position:absolute;left:154px;top:181px;width:108px;height:37px;border-radius:4px;border:1px solid #ffcf70;
  background:linear-gradient(#ffb52e,#f07c00);color:#fff;text-align:center}
.cta small{display:block;font-size:8px;margin-top:4px}
.cta b{display:block;font-size:17px;line-height:18px}
.hero-art{position:absolute;left:306px;top:0;width:306px;height:236px;
  background:linear-gradient(110deg,rgba(255,255,255,0) 0,rgba(160,205,245,.35) 60%,rgba(70,110,170,.5) 100%)}
.features{left:102px;top:360px;width:616px;display:flex;gap:13px}
.feature{width:140px;height:62px;background:#fff;border:1px solid var(--card-border);border-radius:3px;position:relative;padding:8px 6px 0 38px}
.feature svg{position:absolute;left:6px;top:12px}
.feature h3{font-size:13px;font-weight:300;color:var(--link);margin-bottom:3px}
.feature p{font-size:7px;line-height:9px;color:#555}
.rule{left:104px;width:612px;border-top:1px dotted #9aa}
.tagline{left:0;width:818px;top:463px;text-align:center;font-weight:300;color:#222}
.tagline h2{font-size:19px;font-weight:300}
.tagline h2 em{font-style:normal;color:var(--link)}
.tagline p{font-size:14px;margin-top:0}
.about{left:108px;top:533px;width:600px}
.about h2{font-size:18px;font-weight:300;color:var(--link);margin-bottom:12px}
.about p{font-size:7px;line-height:11.6px;margin-bottom:11.5px;color:#333}
.about em{font-style:normal;color:var(--link)}
.offers{left:102px;top:703px;width:612px;height:109px;background:#cfe6f8;border-radius:4px}
.offer{position:absolute;top:7px;width:140px;height:93px;border-radius:2px;overflow:hidden;font-family:"Anton",Impact,sans-serif;color:#fff;padding:6px 10px}
.offer .big{position:relative;z-index:1;font-size:20px;line-height:21px;text-shadow:1px 1px 0 rgba(0,0,0,.35)}
.offer .sub{font-family:"Roboto",Arial,sans-serif;font-size:8px;font-weight:700;color:#ffe100}
.offer .foot{position:absolute;left:0;bottom:0;width:100%;height:18px;background:rgba(0,0,0,.35);font-family:"Roboto",Arial,sans-serif;font-size:8.5px;text-align:center;line-height:18px}
.offer .ribbon{position:absolute;right:-18px;top:12px;width:80px;height:16px;transform:rotate(45deg);background:#e0321b;font-family:"Roboto",Arial,sans-serif;font-size:8px;font-weight:700;text-align:center;line-height:16px}
.offer-free{left:7px;background:linear-gradient(#e8241a,#b3120c)}
.offer-free .big{color:#ffe100}
.offer-free .ribbon{background:#1c6fd1}
.offer-pro{left:158px;background:linear-gradient(#f29a16,#d24d0a)}
.offer-turbo{left:308px;background:linear-gradient(#4cb325,#1d7410)}
.offer-turbo .big{font-size:16px;line-height:19px}
.offer-turbo .foot{height:28px;line-height:12px;padding-top:2px}
.how{position:absolute;left:468px;top:14px;width:136px}
.how h4{font-family:"Anton",Impact,sans-serif;font-weight:400;font-size:11px;color:#222;margin-bottom:6px;letter-spacing:.2px}
.how p{font-size:7px;line-height:11.5px;color:#333;text-align:justify}
.examples{left:128px;top:852px;width:150px}
.examples h3{font-size:11px;font-weight:400;color:var(--link);line-height:12px;margin-bottom:12px}
.examples p{font-size:7px;line-height:11.6px;color:#444}
.examples .more{display:block;text-align:right;font-size:7.5px;color:var(--link);margin-top:16px}
.shots{left:342px;top:846px;width:304px;height:116px;background:linear-gradient(90deg,#dcdcdc,#f5f5f5 30%,#e6e6e6 70%,#2b3a55)}
.shot-main{left:384px;top:842px;width:208px;height:124px;border:3px solid var(--green);background:linear-gradient(#2a2a2a 0,#2a2a2a 18%,#f4f4f4 18%,#e8edf2 100%)}
.footer{left:0;top:1000px;width:818px;height:200px;background:var(--footer);border-top:4px solid #4aa8ea}
.foot-brand{left:102px;top:990px;width:116px;height:60px;background:linear-gradient(#3a9fe6,#1c74c7);display:flex;align-items:center;justify-content:center;gap:5px}
.foot-brand .dot{width:20px;height:20px;border-radius:50%;background:#0e3e6e}
.foot-brand span{font-size:20px;color:#0e3e6e}
.col{top:1028px;color:var(--footer-text)}
.col h5{font-size:13px;font-weight:400;color:#ddd;display:flex;align-items:center;gap:8px;height:22px;border-bottom:1px solid var(--footer-line);padding-bottom:3px;margin-bottom:4px}
.col ul{list-style:none;font-size:7.5px}
.col li{height:19px;line-height:19px;border-bottom:1px solid var(--footer-line);padding-left:8px;position:relative}
.col li::before{content:"";position:absolute;left:1px;top:8px;border:2px solid transparent;border-left:3px solid var(--link)}
.follow{left:112px;top:1066px;color:#bbb;font-size:12px}
.social{left:112px;top:1085px;display:flex;gap:12px}
.social span{width:20px;height:20px;border-radius:50%;background:#f2f2f2;border:2px solid #ccc}
.email{left:608px;top:1066px;width:85px;height:15px;background:#fff;border:1px solid #999;font-size:7px;color:#aaa;font-style:italic;padding:3px 5px}
.plus{left:693px;top:1065px;width:17px;height:17px;background:var(--green);display:flex;align-items:center;justify-content:center}
.like{left:608px;top:1108px;display:flex;gap:3px;font-size:7px}
.like .btn{background:#eceef5;border:1px solid #9aa;padding:1px 4px;color:#333;display:flex;align-items:center;gap:3px}
.like .btn i{width:7px;height:7px;background:#3b5998;display:inline-block}
.like .count{background:#fff;border:1px solid #9aa;padding:1px 3px;color:#333}
.copy{left:0;width:818px;top:1163px;text-align:center;font-size:7.5px;color:#ccc}
.copy em{font-style:normal;color:var(--link)}
</style>
</head>
<body>
<div class="abs top-bar"></div>
<nav class="abs top-nav"><span>ABOUT US</span><span class="sep">|</span><span>CONTACT US</span><span class="sep">|</span><span>LOGIN</span></nav>

<div class="abs brand"><div class="brand-dot"></div><div class="brand-name">zAvora</div></div>

<nav class="abs menu">
  <div class="home"><svg width="18" height="14" viewBox="0 0 18 14"><path d="M9 1 L17 8 H14 V13 H4 V8 H1 Z" fill="#fff"/></svg></div>
  <span>Quick Tour</span><span>Pricing</span>
</nav>

<section class="abs hero">
  <div class="hero-art" role="img" aria-label="Illustration of a puzzled business owner surrounded by speech bubbles of online marketing terms"></div>
  <h1>Getting a website has never<br>been so simple</h1>
  <ul>
    <li><svg viewBox="0 0 16 12"><path d="M0 4 H8 V0 L16 6 L8 12 V8 H0 Z" fill="#fff"/></svg>Business Websites</li>
    <li><svg viewBox="0 0 16 12"><path d="M0 4 H8 V0 L16 6 L8 12 V8 H0 Z" fill="#fff"/></svg>Online Marketing</li>
    <li><svg viewBox="0 0 16 12"><path d="M0 4 H8 V0 L16 6 L8 12 V8 H0 Z" fill="#fff"/></svg>Dashboard Controls</li>
    <li><svg viewBox="0 0 16 12"><path d="M0 4 H8 V0 L16 6 L8 12 V8 H0 Z" fill="#fff"/></svg>Full Setup &amp; Support</li>
  </ul>
  <div class="cta"><small>Sign up NOW for</small><b>FREE!</b></div>
</section>

<div class="abs features">
  <div class="feature">
    <svg width="26" height="26" viewBox="0 0 26 26"><rect x="1" y="10" width="5" height="14" fill="#2b8ee0"/><rect x="8" y="4" width="5" height="20" fill="#2b8ee0"/><rect x="15" y="14" width="5" height="10" fill="#2b8ee0"/><rect x="0" y="24" width="26" height="2" fill="#2b8ee0"/></svg>
    <h3>Case Studies</h3><p>Read real stories about small businesses online</p>
  </div>
  <div class="feature">
    <svg width="22" height="28" viewBox="0 0 22 28"><circle cx="11" cy="10" r="8" fill="none" stroke="#2b8ee0" stroke-width="2"/><rect x="7" y="19" width="8" height="6" fill="none" stroke="#2b8ee0" stroke-width="2"/></svg>
    <h3>How to</h3><p>Learn from our online market-ing tips for small business</p>
  </div>
  <div class="feature">
    <svg width="28" height="24" viewBox="0 0 28 24"><path d="M2 2 H20 V14 H8 L4 18 V14 H2 Z" fill="#2b8ee0"/><path d="M10 8 H26 V20 H24 V23 L21 20 H10 Z" fill="#5cb0ee"/></svg>
    <h3>News &amp; Chatter</h3><p>Get up-to-date news and chatter about online marketing</p>
  </div>
  <div class="feature">
    <svg width="26" height="26" viewBox="0 0 26 26"><circle cx="13" cy="14" r="11" fill="none" stroke="#2b8ee0" stroke-width="2"/><path d="M13 7 V14 L18 17" stroke="#2b8ee0" stroke-width="2" fill="none"/></svg>
    <h3>Demo</h3><p>Find out what zAvora can do for your business.</p>
  </div>
</div>

<div class="abs rule" style="top:448px"></div>
<div class="abs tagline">
  <h2>The Complete Online Marketing Solution for <em>Small Business Websites</em></h2>
  <p>“Get a big online presence and more sales leads in 30 minutes”</p>
</div>
<div class="abs rule" style="top:514px"></div>

<section class="abs about">
  <h2>About Us</h2>
  <p><em>zAvora</em> will build your business website, optimise SEO marketing and make recommendations on best practices to help you win customers. Let our team of experts design a business website for you. Choose a business website from <em>zAvora's</em> broad array of fabulous, customisable business websites and our experts will have your business online in minutes. <em>zAvora</em> lets you create a professional business website without the need to know how to code or programme.</p>
  <p>Your business website comes with automatic Internet marketing, marketing on the Internet is easy with <em>zAvora</em>, we automatically optimise your site for SEO marketing and we can run Adnetra ad campaigns when you need them. Get a business website with online marketing now. <em>zAvora</em> brings your Small Business Website to LIFE!</p>
  <p>View our example business websites above, watch the video demo to see how to make a business website or call us now and get your business marketing online today. The <em>zAvora</em> website builder gives you a professional online appearance - post your own images, give customers your latest news and create customer testimonials, it's the most complete online marketing solution for your business.</p>
</section>

<section class="abs offers">
  <div class="offer offer-free"><div class="big">Free<br>SETUP</div><div class="ribbon">£199 Value</div><div class="foot">WEB OFFER ONLY</div></div>
  <div class="offer offer-pro"><div class="big">Pro<br>PACKAGE</div><div class="sub">Big online presence</div><div class="ribbon">£22 /month</div><div class="foot">Business Website &amp; Easy Dashboard</div></div>
  <div class="offer offer-turbo"><div class="ribbon">£29 /month</div><div class="big">TURBO SALES<br>PRO PLUS</div><div class="sub">More sales LEADS</div><div class="foot">Business Website,<br>Easy Dashboard &amp; ppc Sales</div></div>
  <div class="how"><h4>How does it work?</h4><p>Neque porro quisquam est qui do-lorem ipsum quia dolor vel eum iriure dolor in hendrerit in vulputate velit dou site vesse molestie consequat, vel illumsit amet, adipisci velit"</p></div>
</section>

<section class="abs examples">
  <h3>View examples of our<br>stunning business websites</h3>
  <p>Duis autem vel eum iriure dolor in hen-drerit in vulputate velit esse molestie consequat, vel illum dolore eu feugiat nulla facilisis at vero eros et accumsan. esse molestie.</p>
  <span class="more">&#9702; View more</span>
</section>
<svg class="abs" style="left:306px;top:882px" width="14" height="28" viewBox="0 0 14 28"><path d="M14 0 V28 L0 14 Z" fill="#7a8a96"/></svg>
<div class="abs shots" role="img" aria-label="Example business website screenshots"></div>
<div class="abs shot-main" role="img" aria-label="Featured example business website screenshot"></div>
<svg class="abs" style="left:662px;top:882px" width="14" height="28" viewBox="0 0 14 28"><path d="M0 0 V28 L14 14 Z" fill="#6cc0ef"/></svg>

<footer class="abs footer"></footer>
<div class="abs foot-brand"><div class="dot"></div><span>zAvora</span></div>
<div class="abs follow">Follow</div>
<div class="abs social"><span></span><span></span><span></span></div>

<div class="abs col" style="left:226px;width:138px">
  <h5><svg width="20" height="20" viewBox="0 0 20 20"><circle cx="10" cy="10" r="7" fill="none" stroke="#777" stroke-width="4" stroke-dasharray="3 2"/><circle cx="10" cy="10" r="3" fill="#777"/></svg>OurServices</h5>
  <ul><li>Search Engine Optimization (SEO)</li><li>Social Media</li><li>Web Analytics</li></ul>
</div>
<div class="abs col" style="left:376px;width:104px">
  <h5><svg width="18" height="24" viewBox="0 0 18 24"><rect x="1" y="1" width="16" height="22" rx="3" fill="#777"/><rect x="4" y="4" width="10" height="14" fill="#1d1d1d"/></svg>ContactUs</h5>
  <ul><li>Contact Us</li><li>Customer Support</li><li>Request a call back</li><li>FAQ's</li></ul>
</div>
<div class="abs col" style="left:490px;width:104px">
  <h5><svg width="24" height="20" viewBox="0 0 24 20"><path d="M1 3 H9 L11 5 H23 V19 H1 Z" fill="#777"/></svg>Navigation</h5>
  <ul><li>Site Map</li><li>Terms and Condition</li><li>Privacy &amp; Policy</li><li>Get in Touch</li></ul>
</div>
<div class="abs col" style="left:608px;width:102px">
  <h5><svg width="26" height="18" viewBox="0 0 26 18"><rect x="1" y="1" width="24" height="16" fill="#777"/><path d="M1 1 L13 10 L25 1" stroke="#1d1d1d" stroke-width="1.5" fill="none"/></svg>Subscribe</h5>
</div>
<div class="abs email">Type your email here</div>
<div class="abs plus"><svg width="9" height="9" viewBox="0 0 9 9"><path d="M3 0 H6 V3 H9 V6 H6 V9 H3 V6 H0 V3 H3 Z" fill="#fff"/></svg></div>
<div class="abs like"><span class="btn"><i></i>Like</span><span class="count">62</span></div>

<div class="abs copy">Copyright © 2011 zAvora Pvt. Ltd 2011 - All rights reserved. Managed by <em>zAvora</em> &nbsp;|&nbsp; Admin</div>
</body>
</html>
```